Business card design for Automotive workshop

We need a business card for a new automotive repair and tyre shop called Keelstone Prime Automotive located in New Zealand. We are a clean, modern and fresh workshop and company.

Front needs to feature logo,
my name:
Marlo Fenwicke (director)

Address:
48 Tarn Lane
Whitianga 3510

Phone: 07 594 2713
Mobile: 027 451 9362
Email: office@keelstoneautomotive.example.nz
Website: keelstoneautomotive.example.nz

Back needs to feature an area to write down appointment details, date and time.

Also feature a list of jobs and work we do such as,
Vehicle Servicing
All Mechanical Repairs
Warrant of Fitness
Tyres & Wheel Alignments
Automotive Diagnostics
Automotive Parts & Supplies

```html
<!DOCTYPE html>
<html lang="en">
<head>
<meta charset="utf-8">
<title>Keelstone Prime Automotive – Business Card</title>
<link href="https://fonts.googleapis.com/css2?family=Roboto:wght@400;500;700&display=swap" rel="stylesheet">
<style>
  :root {
    --backdrop: #3a3330;
    --card: #161616;
    --red: #e41e26;
    --white: #f2f2f2;
    --grey: #b9b9b9;
    --rule: #6a6a6a;
  }
  * { box-sizing: border-box; margin: 0; padding: 0; }
  html, body { width: 1200px; height: 716px; overflow: hidden; }
  body {
    background: var(--backdrop);
    font-family: "Roboto", sans-serif;
    position: relative;
  }
  .card {
    position: absolute;
    top: 203px;
    width: 540px;
    height: 310px;
    background: var(--card);
    border-radius: 3px;
    box-shadow: 0 14px 30px rgba(0,0,0,.45);
    overflow: hidden;
  }
  .card--back { left: 40px; }
  .card--front { left: 620px; }

  .brand {
    display: flex;
    align-items: center;
    gap: 12px;
    color: var(--red);
    font-weight: 700;
    text-transform: uppercase;
    line-height: 1.05;
  }
  .brand__mark {
    width: 14px; height: 14px;
    background: var(--red);
    flex: none;
  }
  .brand__name { font-size: 28px; letter-spacing: 1px; }
  .brand__name small { display: block; font-size: 28px; }

  .card--back .brand {
    position: absolute; left: 0; right: 0; top: 34px;
    justify-content: center;
  }
  .services {
    position: absolute; left: 30px; right: 30px; top: 122px;
    list-style: none;
    display: flex; flex-wrap: wrap; justify-content: center;
    gap: 8px 16px;
    color: var(--white);
    font-size: 13px;
  }
  .services li { display: flex; align-items: center; gap: 6px; }
  .services li::before {
    content: ""; width: 6px; height: 6px; border-radius: 50%;
    background: var(--red);
  }

  .appointment {
    position: absolute; left: 40px; right: 40px; top: 212px;
    color: var(--white);
  }
  .appointment__title {
    color: var(--red); font-size: 12px; font-weight: 500;
    text-transform: uppercase; letter-spacing: 1.5px;
    margin-bottom: 14px;
  }
  .appointment__fields { display: flex; gap: 24px; }
  .appointment__field {
    flex: 1; display: flex; align-items: flex-end; gap: 8px;
    font-size: 13px; color: var(--grey);
  }
  .appointment__field span:last-child {
    flex: 1; height: 1px; background: var(--rule); margin-bottom: 3px;
  }

  .card--front .brand { position: absolute; right: 34px; top: 44px; }
  .person {
    position: absolute; right: 330px; top: 170px;
    text-align: right;
  }
  .person__name {
    color: var(--red); font-size: 20px; font-weight: 400;
    text-transform: uppercase; letter-spacing: .5px; white-space: nowrap;
  }
  .person__role { color: var(--white); font-size: 16px; margin-top: 2px; }
  .person__address { color: var(--grey); font-size: 13px; margin-top: 12px; line-height: 1.45; }
  .divider {
    position: absolute; left: 224px; top: 170px;
    width: 1px; height: 100px; background: var(--white);
  }
  .contacts {
    position: absolute; left: 238px; top: 172px;
    list-style: none; color: var(--white); font-size: 13px;
  }
  .contacts li { display: flex; align-items: center; gap: 8px; height: 23px; white-space: nowrap; }
  .contacts svg { width: 13px; height: 13px; fill: var(--red); flex: none; }
</style>
</head>
<body>

<section class="card card--back" aria-label="Card back">
  <div class="brand">
    <span class="brand__mark"></span>
    <span class="brand__name">Keelstone Prime<small>Automotive</small></span>
  </div>
  <ul class="services">
    <li>Vehicle Servicing</li>
    <li>All Mechanical Repairs</li>
    <li>Warrant of Fitness</li>
    <li>Tyres &amp; Wheel Alignments</li>
    <li>Automotive Diagnostics</li>
    <li>Automotive Parts &amp; Supplies</li>
  </ul>
  <div class="appointment">
    <p class="appointment__title">Your Next Appointment</p>
    <div class="appointment__fields">
      <p class="appointment__field"><span>Date</span><span></span></p>
      <p class="appointment__field"><span>Time</span><span></span></p>
    </div>
  </div>
</section>

<section class="card card--front" aria-label="Card front">
  <div class="brand">
    <span class="brand__mark"></span>
    <span class="brand__name">Keelstone Prime<small>Automotive</small></span>
  </div>

  <div class="person">
    <p class="person__name">Marlo Fenwicke</p>
    <p class="person__role">Director</p>
    <p class="person__address">48 Tarn Lane<br>Whitianga 3510</p>
  </div>

  <span class="divider"></span>

  <ul class="contacts">
    <li>
      <svg viewBox="0 0 16 16" aria-hidden="true"><path d="M4 0h8a1 1 0 0 1 1 1v14a1 1 0 0 1-1 1H4a1 1 0 0 1-1-1V1a1 1 0 0 1 1-1zm1 2v10h6V2zm3 11a1 1 0 1 0 0 2 1 1 0 0 0 0-2z"/></svg>
      027 451 9362
    </li>
    <li>
      <svg viewBox="0 0 16 16" aria-hidden="true"><path d="M1 4c2-3 12-3 14 0v2h-4V4H5v2H1zM3 7h10l2 8H1zm5 2a2 2 0 1 0 0 4 2 2 0 0 0 0-4z"/></svg>
      07 594 2713
    </li>
    <li>
      <svg viewBox="0 0 16 16" aria-hidden="true"><path d="M0 3h16v10H0zm1.5 1.5L8 9l6.5-4.5V4h-13z"/></svg>
      office@keelstoneautomotive.example.nz
    </li>
    <li>
      <svg viewBox="0 0 16 16" aria-hidden="true"><circle cx="8" cy="8" r="7.5"/><path d="M.5 8h15M8 .5c-4 4-4 11 0 15M8 .5c4 4 4 11 0 15" stroke="#161616" stroke-width="1" fill="none"/></svg>
      keelstoneautomotive.example.nz
    </li>
  </ul>
</section>

</body>
</html>
```